Business card for law firm

Need business card for new law firm. Think confident, authoritative, conservative, but not stuffy or old-fashioned.

Contact Information for Business Card

Content for card - logo (uploaded), plus the following:

Paul Whitcombe (larger font)
Managing Partner (larger font, but not as large as name)
Level 9, 7 Ferris Lane
Sydney NSW 2000
Main Tel 02 9364 2710
Direct Tel 02 8472 3159
Email paul@qvlegal.com.au
www.qvlegal.com.au

Letterhead design should include logo plus:
Level 9, 7 Ferris Lane
Sydney NSW 2000
Tel 02 8472 3159
www.qvlegal.com.au

```html
<!DOCTYPE html>
<html lang="en">
<head>
<meta charset="utf-8">
<title>Quayvale Legal — Business Card</title>
<link rel="stylesheet" href="https://fonts.googleapis.com/css2?family=Cinzel:wght@400&family=Open+Sans:wght@400;700&display=swap">
<style>
  :root {
    --navy: #001a55;
    --ink: #1a1a1a;
    --black: #050505;
    --white: #ffffff;
    --stage-light: #ececec;
    --stage-dark: #c6c7ca;
    --edge: #a8a8a8;
  }
  * { box-sizing: border-box; margin: 0; padding: 0; }
  html, body {
    width: 1200px; height: 1141px; overflow: hidden;
  }
  body {
    position: relative;
    background: linear-gradient(135deg, var(--stage-light) 0%, var(--stage-dark) 100%);
    font-family: "Open Sans", Arial, sans-serif;
    color: var(--ink);
  }
  .card {
    position: absolute;
    width: 757px; height: 432px;
    border-radius: 40px;
    overflow: hidden;
  }

  /* Front */
  .card-front {
    left: 369px; top: 87px;
    background: var(--white);
    border: 1px solid var(--edge);
  }
  .name-bar {
    position: absolute; left: 0; top: 59px;
    width: 15px; height: 47px;
    background: var(--navy);
  }
  .person-name {
    position: absolute; left: 24px; top: 53px;
    font-size: 25px; font-weight: 700; color: var(--navy);
    letter-spacing: 0.3px;
  }
  .person-title {
    position: absolute; left: 24px; top: 87px;
    font-size: 19px; font-weight: 400; color: var(--ink);
    letter-spacing: 0.3px;
  }
  .contact-list {
    position: absolute; left: 24px; top: 186px;
    list-style: none;
    font-size: 19px; line-height: 32px;
  }
  .contact-list li { display: flex; align-items: center; gap: 6px; }
  .contact-icon { width: 16px; height: 16px; flex: none; }
  .address {
    position: absolute; left: 24px; top: 299px;
    font-size: 19px; line-height: 30px; font-style: normal;
  }
  .firm-name {
    position: absolute; right: 40px; top: 126px;
    font-family: "Cinzel", "Times New Roman", serif;
    font-size: 30px; font-weight: 400; color: var(--navy);
    letter-spacing: 1px;
  }
  .footer-band {
    position: absolute; left: 0; bottom: 0;
    width: 757px; height: 58px; display: block;
  }
  .footer-web {
    position: absolute; left: 24px; bottom: 30px;
    font-size: 19px; color: var(--white);
    letter-spacing: 3.2px;
  }

  /* Back */
  .card-back {
    left: 70px; top: 579px;
    background: var(--navy);
  }
  .back-firm-name {
    position: absolute; left: 34px; top: 62px;
    font-family: "Cinzel", "Times New Roman", serif;
    font-size: 44px; font-weight: 400; color: var(--white);
    letter-spacing: 1px;
  }
  .back-web {
    position: absolute; right: 74px; bottom: 33px;
    font-size: 24px; color: var(--white);
    letter-spacing: 3.4px;
  }
  .back-web strong { font-weight: 700; }
</style>
</head>
<body>

  <section class="card card-front" aria-label="Business card front">
    <span class="name-bar"></span>
    <h1 class="person-name">PAUL WHITCOMBE</h1>
    <p class="person-title">MANAGING PARTNER</p>

    <ul class="contact-list">
      <li>
        <svg class="contact-icon" viewBox="0 0 16 16" aria-hidden="true">
          <circle cx="8" cy="8" r="7" fill="none" stroke="#1a1a1a" stroke-width="1.4"/>
          <path d="M5.6 4.2c-.8.4-1 1.6-.4 3.2.7 1.8 2 3.4 3.4 4.2.9.5 1.7.4 2.1-.2l-1.6-1.6-.9.5c-.7-.5-1.4-1.5-1.8-2.4l.8-.6-.8-2.1z" fill="#1a1a1a"/>
        </svg>
        02 9364 2710(Main)
      </li>
      <li>
        <svg class="contact-icon" viewBox="0 0 16 16" aria-hidden="true">
          <circle cx="8" cy="8" r="7" fill="none" stroke="#1a1a1a" stroke-width="1.4"/>
          <path d="M5.6 4.2c-.8.4-1 1.6-.4 3.2.7 1.8 2 3.4 3.4 4.2.9.5 1.7.4 2.1-.2l-1.6-1.6-.9.5c-.7-.5-1.4-1.5-1.8-2.4l.8-.6-.8-2.1z" fill="#1a1a1a"/>
        </svg>
        02 8472 3159(Direct)
      </li>
      <li>
        <svg class="contact-icon" viewBox="0 0 16 16" aria-hidden="true">
          <path d="M1 6.5 8 2l7 4.5V14H1z" fill="#001a55"/>
          <path d="M1 6.5 8 11l7-4.5" fill="none" stroke="#fff" stroke-width="1.3"/>
        </svg>
        paul@qvlegal.com.au
      </li>
    </ul>

    <address class="address">
      Level 9, 7 Ferris Lane<br>
      Sydney NSW 2000
    </address>

    <p class="firm-name">QUAYVALE LEGAL</p>

    <svg class="footer-band" viewBox="0 0 757 58" aria-hidden="true">
      <rect x="0" y="0" width="757" height="58" fill="#001a55"/>
      <path d="M0 0H507C490 0 490 32 468 32H0Z" fill="#050505"/>
    </svg>
    <span class="footer-web">www.qvlegal.com.au</span>
  </section>

  <section class="card card-back" aria-label="Business card back">
    <p class="back-firm-name">QUAYVALE LEGAL</p>
    <p class="back-web">www.<strong>qvlegal</strong>.com.au</p>
  </section>

</body>
</html>
```